Tallreed Agency Website

We need a website design for a UK based marketing and PR agency called "Tallreed Agency". We are a small and vibrant team that looks after a mixture of clients from the luxury lifestyle and professional services sectors so the design needs to reflect this and convey: Professionalism, contemporary approach, creativity and the high end luxury and professional market we look after. Our services include marketing, PR, social media and copywriting and we look after both local and national clients. The design will need to incorporate the grey and orange brand colours (logo attached) but we are open to the use of more/different colours - with the possibility of a slight refresh on the current logo/branding. The main pages required include: Home, About Us, Services, Sectors, Case Studies and Blog.

ur existing website can be seen here - http://www.tallreed-example.co.uk

The site will need to showcase our approach, services and expertise, existing/previous clients, and provide frequently updated content via news and blog to support our marketing campaigns.

The key objectives for the site are:
- To support current sales activity by giving potential clients somewhere to visit to find out who we are, what we can do, what we have done
- To generate incoming sales leads/enquiries from companies looking for marketing and PR services
- To showcase us as a high end a professional agency with some fantastic clients and a wealth of experience

Target Market(s)

Professional services e.g. accountants, data centres etc
Luxury lifestyle e.g. wedding venue, tailor, homeware etc.
British market - mainly South East/London
Small - Medium sized businesses

Industry/Entity Type

Marketing

Font styles to use
Other font styles liked:
• Din Regular and Bold is currently used

Colors
f78f20
aaaaaa

Requirements
Must have
• Must Have:
- The main menu items are likely to be:
- Services
- Sectors
- About us
- Case Studies
- Blog
- Contact us

Some of these items may have a sub-menu, e.g. About us is likely to have "Company", "Team", and "Careers" below it and "Services" will have "marketing", "PR", "Copywriting", "Social media". Sectors will have "Professional", "Luxury", "Lifestyle"

Key must-have elements of the homepage include:
- Social media icons (twitter, linkedin, facebook, google+)
- Contact details (i.e. phone number and email/link)
- "We have worked with..." - this is likely to be icons for logos of previous and current clients
- "Sign up to newsletter"
- "Latest news"

Footer navigation must allow for the usual suspects (sitemap, t's & c's, privacy policy, company registration details)

Some kind of call-to-action boxes/areas/links to provide us with ways to link out to any specific micro-sites or pages within the site (e.g. to highlight some of our specific case studies, services etc).

To confirm, we are looking for the following page types/templates:
1) Home page
2) Inside/content page (can be used for services, about us etc)
3) Article page (for blog/news articles etc)
4) Case studies (an image led pad to showcase campaigns we have worked on)
4) Contact page
Nice to have
• - If web fonts are needed for the design, then please note we have an existing web fonts account with typevault-example.com and so can use any of the web fonts available there.
Should not have
• We do not want to use a one page-scroll down website

```html
<!DOCTYPE html>
<html lang="en">
<head>
<meta charset="utf-8">
<title>Tallreed Agency – Services</title>
<link href="https://fonts.googleapis.com/css2?family=Lato:wght@400;700&family=Montserrat:wght@400;500&family=Barlow:wght@500&display=swap" rel="stylesheet">
<style>
:root{
  --orange:#f78f20;
  --grey:#aaaaaa;
  --header:#2e2e2e;
  --header-active:#1e1e1e;
  --titlebar:#f3f3f3;
  --ink:#2b2b2b;
  --body-text:#9a9a9a;
  --connect:#333333;
  --footer:#3b3b3b;
  --footer-bottom:#2a2a2a;
  --footer-text:#9c9c9c;
  --white:#ffffff;
}
*{margin:0;padding:0;box-sizing:border-box}
html,body{width:702px;height:1200px;overflow:hidden;background:var(--white)}
body{position:relative;font-family:"Lato",Arial,sans-serif;color:var(--ink)}
a{color:inherit;text-decoration:none}
.abs{position:absolute}

/* header */
.site-header{position:absolute;left:0;top:0;width:702px;height:45px;background:var(--header)}
.brand{position:absolute;left:93px;top:12px;font-family:"Barlow",sans-serif;font-weight:500;font-size:17px;color:var(--orange);letter-spacing:.2px}
.main-nav a{position:absolute;top:0;height:45px;line-height:45px;font-size:7.5px;color:#c9c9c9;text-align:center}
.main-nav a.active{background:var(--header-active);color:var(--white);font-weight:700}

/* title bar */
.title-bar{position:absolute;left:0;top:45px;width:702px;height:51px;background:var(--titlebar)}
.page-title{position:absolute;left:93px;top:20px;font-size:10px;color:#333}
.breadcrumb{position:absolute;right:92px;top:22px;font-size:5.5px;color:#888}
.breadcrumb b{color:#333;font-weight:700}

/* banner */
.banner-visual{position:absolute;left:50px;top:96px;width:586px;height:129px;
  background:linear-gradient(90deg,#e2ddd9 0%,#f0ecea 25%,#fafafa 55%,#f6f1f1 80%,#fbfbfb 100%)}
.banner-title{position:absolute;left:0;top:150px;width:702px;text-align:center;font-family:"Montserrat",sans-serif;font-weight:500;font-size:16px;letter-spacing:1px;color:#222}
.banner-rule{position:absolute;top:160px;height:1px;width:66px;background:#444}

/* tabs */
.tab{position:absolute;top:242px;width:72px;height:19px;line-height:17px;border:1px solid #d4d4d4;text-align:center;font-size:8px;color:#333;background:var(--white)}
.tab.active{background:var(--orange);border-color:var(--orange);color:var(--white)}
.intro{position:absolute;left:196px;top:276px;width:310px;text-align:center;font-size:7px;line-height:11.5px;color:#333}

/* services list */
.service-media{position:absolute;left:94px;width:206px;height:110px}
.service-title{position:absolute;left:313px;font-size:8px;color:#333}
.service-text{position:absolute;left:313px;width:294px;font-size:6.4px;line-height:12px;color:var(--body-text)}

/* footer */
.connect-bar{position:absolute;left:0;top:1017px;width:702px;height:30px;background:var(--connect)}
.connect-label{position:absolute;left:95px;top:10px;font-size:8px;font-weight:700;color:#ddd}
.social-dot{position:absolute;top:1027px;width:10px;height:10px;border-radius:50%;background:#666}
.site-footer{position:absolute;left:0;top:1047px;width:702px;height:124px;background:var(--footer)}
.footer-heading{position:absolute;top:1059px;font-size:8px;font-weight:700;color:#eee}
.footer-text{position:absolute;font-size:6.5px;line-height:13px;color:var(--footer-text)}
.footer-text u{color:#ddd}
.email-field{position:absolute;left:357px;top:1108px;width:120px;height:17px;background:var(--white);border:1px solid #ccc;font-size:5.5px;color:#999;padding:5px 6px}
.subscribe{position:absolute;left:414px;top:1133px;width:63px;height:16px;line-height:16px;text-align:center;background:#5b5b5b;color:var(--white);font-size:6.5px;font-weight:700}
.blog-thumb{position:absolute;left:489px;top:1081px;width:28px;height:28px;background:linear-gradient(135deg,#b8876b,#6c5a6e)}
.blog-title{position:absolute;left:522px;top:1079px;width:90px;font-size:6.8px;line-height:11px;color:#eee}
.blog-date{position:absolute;left:522px;top:1101px;font-size:5px;color:#8a8a8a}
.blog-excerpt{position:absolute;left:522px;top:1110px;width:80px;font-size:5.8px;line-height:10px;color:var(--footer-text)}
.blog-link{position:absolute;left:522px;top:1138px;font-size:5.8px;color:var(--orange);font-weight:700}
.footer-bottom{position:absolute;left:0;top:1171px;width:702px;height:29px;background:var(--footer-bottom)}
.copyright{position:absolute;left:95px;top:12px;font-size:6.5px;color:#8a8a8a}
.footer-nav{position:absolute;right:93px;top:12px;font-size:6.5px;color:#9a9a9a}
.footer-nav a{margin-left:9px}
</style>
</head>
<body>

<header class="site-header">
  <div class="brand">Tallreed Agency</div>
  <nav class="main-nav">
    <a class="active" style="left:234px;width:49px">Home</a>
    <a style="left:288px;width:45px">About Us</a>
    <a style="left:343px;width:46px">Services</a>
    <a style="left:398px;width:43px">Sectors</a>
    <a style="left:452px;width:58px">Case Studies</a>
    <a style="left:522px;width:30px">Blog</a>
    <a style="left:565px;width:48px">Contact Us</a>
  </nav>
</header>

<section class="title-bar">
  <h1 class="page-title" style="font-weight:400">Services</h1>
  <div class="breadcrumb">Home &nbsp;/&nbsp; Features &nbsp;/&nbsp; Shortcodes &nbsp;/&nbsp; <b>Services</b></div>
</section>

<div class="banner-visual" role="img" aria-label="Soft faded photo of a person at work with hand-written marketing words: list creation, email marketing, branding, goals"></div>
<div class="banner-rule" style="left:230px"></div>
<div class="banner-rule" style="left:416px"></div>
<h2 class="banner-title" style="font-weight:500">SERVICES</h2>

<div class="tab active" style="left:221px">Marketing</div>
<div class="tab" style="left:297px">PR Services</div>
<div class="tab" style="left:372px">Social media</div>
<div class="tab" style="left:448px">Copywriting</div>

<p class="intro">With our strong background in both the strategy and delivery of marketing campaigns, we are able to offer effective and measurable solutions tailored to your specific business requirements. By combining tactical thinking with creativity, we ensure that all communications are delivered consistently across all media platforms.</p>

<div class="service-media" style="top:339px;background:linear-gradient(135deg,#3a3a3c,#1d1d1f 55%,#cfcfd2 75%,#9a9a9c)" role="img" aria-label="Dark branded stationery set with letterhead and pen"></div>
<h3 class="service-title" style="top:339px;font-weight:400">Branding</h3>
<p class="service-text" style="top:352px">Whether seeking to build a new brand or refresh an existing identity for your business, we can work with you to establish, maintain and ensure consistency of your brand. Working closely with a team of designers we create branding that reflects the unique vision and identity of your business. We can also help translate your brand into successful marketing and PR campaigns that will make you stand out from the crowd to boost your visibility.</p>

<div class="service-media" style="top:475px;background:linear-gradient(180deg,#5a5a5a,#2a2a2a 40%,#1a1a1a 75%,#c9c9c9 85%,#8f8f8f)" role="img" aria-label="Desktop monitor showing a dark portfolio website"></div>
<h3 class="service-title" style="top:476px;font-weight:400">Online</h3>
<p class="service-text" style="top:489px">Your online presence is an increasingly important element to factor into your marketing strategy. We work with you to create an integrated digital marketing campaign which incorporates SEO, blogging, e-newsletters and PPC in order to reach the online masses and drive traffic to your website.</p>

<div class="service-media" style="top:608px;background:linear-gradient(160deg,#e9e9e9,#f5a04a 30%,#f08a1e 60%,#dcdcdc)" role="img" aria-label="Orange and white business cards and envelopes"></div>
<h3 class="service-title" style="top:608px;font-weight:400">Direct Marketing</h3>
<p class="service-text" style="top:622px">We can help you make the most out of your existing data in order to create a dialogue with your current and potential customers, to build your reputation and encourage repeat business. We can also offer advice on procuring databases that are relevant to your target customer profile to build your existing customer base and maximise sales potential.</p>

<div class="service-media" style="top:746px;background:linear-gradient(170deg,#dedede,#2a2a2a 30%,#c9892e 50%,#1f1f1f 70%,#d8d8d8)" role="img" aria-label="Open printed brochure with black and orange layout and photos"></div>
<h3 class="service-title" style="top:746px;font-weight:400">Print</h3>
<p class="service-text" style="top:760px">Print plays a vital role in any marketing campaign in order to translate your brand message and business potential. Working with a team of design and print specialists, we endeavor to work within your budget and timescales to produce collateral of the highest quality. From leaflets, brochures and newsletters to pop-up stands and point of sale, we offer a tailored approach to any size projec</p>

<div class="service-media" style="top:885px;background:linear-gradient(120deg,#e4e4e4,#6f7376 35%,#3d4a52 55%,#9fb3bf 75%,#e0e0e0)" role="img" aria-label="Interior design magazine advertisements with room photos"></div>
<h3 class="service-title" style="top:885px;font-weight:400">Advertising</h3>
<p class="service-text" style="top:899px">At Tallreed Agency we can produce a cost effective advertising campaign tailored to your specific target audience. Whether you have a trade, commercial or consumer focus, we combine creativity with strategic planning and work within your budget to raise brand and product awareness.</p>

<div class="connect-bar"><div class="connect-label">Let's Connect:</div></div>
<div class="social-dot" style="left:508px"></div>
<div class="social-dot" style="left:537px"></div>
<div class="social-dot" style="left:568px"></div>
<div class="social-dot" style="left:596px"></div>

<footer class="site-footer"></footer>
<h4 class="footer-heading" style="left:93px">Contact Us</h4>
<p class="footer-text" style="left:92px;top:1078px">Unit 3, 18 Mill Lane,<br>Westbury, WB4 2QT</p>
<p class="footer-text" style="left:225px;top:1078px">Phone &nbsp;&nbsp;: &nbsp;01632 960 121<br>Fax: &nbsp;&nbsp;&nbsp;&nbsp;&nbsp;&nbsp;: &nbsp;(01) 5550.0199<br>Email &nbsp;&nbsp;&nbsp;: &nbsp;<u>hello@tallreed-example.co.uk</u></p>
<h4 class="footer-heading" style="left:357px">Newsletter Signup</h4>
<p class="footer-text" style="left:357px;top:1077px;width:125px;line-height:11.5px">Phasellus vehicula justo eget diam posuere sollicitudin eu tincidunt nulla.</p>
<div class="email-field">Email address</div>
<div class="subscribe">SUBSCRIBE</div>
<h4 class="footer-heading" style="left:489px">Latest From Blog</h4>
<div class="blog-thumb" role="img" aria-label="Blog post thumbnail photo"></div>
<div class="blog-title">Lorem ipsum dolor sit amet, consectetuer</div>
<div class="blog-date">December 12, 2012 – 9:13 pm</div>
<div class="blog-excerpt">Etiam porta est quis nisi pulvinar ultrices ...</div>
<a class="blog-link">Visit Blog »</a>

<div class="footer-bottom">
  <div class="copyright">© 2013 Harbourline Conferencing</div>
  <nav class="footer-nav"><a>Home</a><a>Teleconferencing</a><a>Web Conferencing</a><a>Pricing</a><a>Resources</a><a>Contact Us</a></nav>
</div>

</body>
</html>
```